Jolly Paws Business Card Update

I have a business card which I love. I want to keep the same logo, colours, font and style. I want to upgrade the scripting and remove some elements and add others.
On the front side under Services - remove the existing wording and insert - Providing individual coaching strategies to create happy, healthy and social canine companions
Under Denise Carvell amend the current wording to read: Qualified in Dog Behavioural Training, Natural Animal Healthcare and Animal Health Science
On the reverse side to remove the web address.

```html
<!DOCTYPE html>
<html lang="en">
<head>
<meta charset="utf-8">
<title>Jolly Paws Business Card</title>
<link rel="stylesheet" href="https://fonts.googleapis.com/css2?family=Open+Sans:wght@400;600;700&family=Arimo:wght@400;700&display=swap">
<style>
  :root {
    --stage: #2a2a2b;
    --blue-deep: #1c3a8a;
    --blue-mid: #1565b5;
    --blue-light: #0a90cf;
    --red-bright: #c81d24;
    --red-dark: #6a1a1c;
    --cream: #ece5cc;
    --cream-light: #f6f1de;
    --navy: #14254f;
    --white: #ffffff;
    --soft-white: #eef1f6;
  }
  * { box-sizing: border-box; margin: 0; padding: 0; }
  html, body { width: 1200px; height: 1138px; overflow: hidden; background: var(--stage); }
  .canvas { position: relative; width: 1200px; height: 1138px; }

  .card {
    position: absolute; left: 275px; width: 622px; height: 376px;
    border-radius: 16px; overflow: hidden;
  }
  .card--front { top: 186px; background: linear-gradient(35deg, var(--blue-deep) 0%, var(--blue-mid) 50%, var(--blue-light) 100%); }
  .card--back  { top: 607px; background: linear-gradient(180deg, var(--blue-light) 0%, var(--blue-mid) 100%); }

  .red-band {
    position: absolute; left: 0; right: 0; bottom: 0;
    background: radial-gradient(ellipse 55% 120% at 60% 60%, var(--red-bright) 0%, #9a1b20 55%, var(--red-dark) 100%);
  }

  /* front */
  .brand-circle {
    position: absolute; border-radius: 50%;
    background: var(--cream); border: 7px solid #b71c22;
  }
  .card--front .brand-circle { left: 236px; top: 35px; width: 150px; height: 150px; }
  .brand-name {
    position: absolute; left: 0; right: 0; top: 194px; text-align: center;
    font-family: "Open Sans", sans-serif; font-weight: 600; font-size: 40px;
    color: var(--soft-white); letter-spacing: 1px; line-height: 44px;
  }
  .tagline {
    position: absolute; left: 0; right: 0; top: 236px; text-align: center;
    font-family: "Open Sans", sans-serif; font-size: 20px; color: var(--soft-white); line-height: 24px;
  }
  .card--front .red-band { top: 302px; }
  .services-pill {
    position: absolute; left: 218px; top: 288px; width: 186px; height: 27px;
    border-radius: 14px; background: linear-gradient(180deg, #ffffff, #d9dde4);
    border: 2px solid var(--blue-mid);
    font-family: "Open Sans", sans-serif; font-weight: 700; font-size: 17px;
    letter-spacing: 2px; color: var(--navy); text-align: center; line-height: 23px;
  }
  .front-services {
    position: absolute; left: 0; right: 0; top: 320px; text-align: center;
    font-family: "Open Sans", sans-serif; font-size: 16px; line-height: 22px; color: #f1dede;
  }

  /* back */
  .card--back .brand-circle {
    left: 98px; top: 55px; width: 120px; height: 120px;
    display: flex; align-items: center; justify-content: center;
  }
  .card--back .brand-circle span {
    font-family: "Open Sans", sans-serif; font-weight: 600; font-size: 17px; color: var(--navy);
  }
  .services-block { position: absolute; left: 261px; top: 66px; font-family: "Arimo", sans-serif; color: var(--white); }
  .services-block h2 { font-weight: 400; font-size: 19px; line-height: 22px; margin-bottom: 10px; }
  .services-block p { font-size: 16.5px; line-height: 19px; }
  .mission-band {
    position: absolute; left: 0; right: 0; top: 203px; height: 30px;
    background: linear-gradient(90deg, var(--cream), var(--cream-light), var(--cream));
    font-family: "Arimo", sans-serif; font-size: 16px; line-height: 30px; text-align: center; color: #1a1a1a;
  }
  .card--back .red-band { top: 233px; }
  .person { position: absolute; left: 0; right: 0; top: 246px; text-align: center; color: var(--soft-white); }
  .person-name { font-family: "Open Sans", sans-serif; font-weight: 600; font-size: 23px; line-height: 28px; }
  .person-role { font-family: "Arimo", sans-serif; font-size: 16px; line-height: 21px; margin-top: 2px; }
  .contacts {
    position: absolute; left: 0; right: 0; top: 324px;
    display: flex; justify-content: center; gap: 16px;
    font-family: "Arimo", sans-serif; font-size: 19px; color: var(--soft-white);
  }
  .contact { display: flex; align-items: center; gap: 6px; }
  .contact svg { width: 17px; height: 17px; }
</style>
</head>
<body>
<main class="canvas">
  <section class="card card--front">
    <div class="brand-circle" aria-hidden="true"></div>
    <div class="brand-name">JOLLY PAWS</div>
    <div class="tagline">HAPPY DOGS, HAPPY OWNERS</div>
    <div class="red-band"></div>
    <div class="services-pill">SERVICES</div>
    <p class="front-services">Providing individual coaching strategies to create happy,<br>healthy and social canine companions</p>
  </section>

  <section class="card card--back">
    <div class="brand-circle"><span>Jolly Paws</span></div>
    <div class="services-block">
      <h2>SERVICES</h2>
      <p>Providing individual coaching<br>strategies to create happy, healthy<br>and social canine companions</p>
    </div>
    <div class="mission-band">Promoting communication and connection between dogs and their families</div>
    <div class="red-band"></div>
    <div class="person">
      <div class="person-name">Denise Carvell</div>
      <div class="person-role">Qualified in Dog Behavioural Training, Natural Animal Healthcare and<br>Animal Health Science</div>
    </div>
    <div class="contacts">
      <span class="contact">
        <svg viewBox="0 0 20 20" aria-hidden="true"><circle cx="10" cy="10" r="9" fill="#e8e8ee"/><rect x="7" y="4.5" width="6" height="11" rx="1.2" fill="#8a1c20"/><rect x="8.2" y="6" width="3.6" height="6" fill="#e8e8ee"/></svg>
        0412 738 265
      </span>
      <span class="contact">
        <svg viewBox="0 0 20 20" aria-hidden="true"><circle cx="10" cy="10" r="9" fill="#e8e8ee"/><rect x="5" y="6.5" width="10" height="7" rx="1" fill="#8a1c20"/><path d="M5.5 7 L10 10.5 L14.5 7" stroke="#e8e8ee" stroke-width="1.2" fill="none"/></svg>
        jollypaws.coach@mail.com
      </span>
    </div>
  </section>
</main>
</body>
</html>
```